Walk Beside The River

Business Card design

Target Market(s)

People who require support in the commnity

Industry/Entity Type

Mental Health Support

Contact Information for Business Card

Mental Health Support Rosalind Tavener walkbesidetheriver@mailcove.com.au 0481 637 092 PO Box 926 Kestrel Bay QLD 4590

Colors
6B429C
8869AF
B7A5CE
E3DAEB
F3F0F8

Requirements
Must have
• Logo & details listed above
Should not have
• No red or orange

```html
<!DOCTYPE html>
<html lang="en">
<head>
<meta charset="utf-8">
<title>Walk Beside The River – Business Card</title>
<link href="https://fonts.googleapis.com/css2?family=Open+Sans:wght@400;600;700;800&display=swap" rel="stylesheet">
<style>
  :root {
    --stage: #232323;
    --card: #1f1e22;
    --card-emboss: #18171b;
    --yellow: #f0e82e;
    --purple: #6b429c;
    --cream: #f3f0e0;
    --white: #f4f4f4;
    --ink: #1f1e22;
  }
  * { box-sizing: border-box; margin: 0; padding: 0; }
  html, body { width: 1200px; height: 780px; overflow: hidden; }
  body {
    background: var(--stage);
    font-family: "Open Sans", sans-serif;
    display: flex;
    align-items: center;
    justify-content: center;
    gap: 40px;
  }
  .card {
    position: relative;
    width: 520px;
    height: 320px;
    background: var(--card);
    border-radius: 22px;
    border: 3px solid var(--yellow);
    overflow: hidden;
  }

  /* back */
  .card-back {
    display: flex;
    align-items: center;
    justify-content: center;
  }
  .back-name {
    font-weight: 700;
    font-size: 28px;
    color: var(--card-emboss);
    white-space: nowrap;
  }

  /* front */
  .name-block {
    position: absolute;
    top: 112px;
    left: 0;
    padding-left: 44px;
  }
  .name-accent {
    position: absolute;
    left: 0;
    top: 6px;
    width: 24px;
    height: 58px;
    background: var(--yellow);
  }
  .person-name {
    font-weight: 800;
    font-size: 30px;
    line-height: 1.1;
    letter-spacing: 0.3px;
    white-space: nowrap;
  }
  .first-name { color: var(--yellow); }
  .last-name { color: var(--purple); }
  .person-title {
    font-size: 14px;
    font-weight: 600;
    color: var(--white);
    margin-top: 4px;
  }

  .logo-badge {
    position: absolute;
    top: 22px;
    right: 30px;
    width: 162px;
    height: 162px;
    border-radius: 50%;
    background: var(--purple);
    display: flex;
    align-items: center;
    justify-content: center;
    text-align: center;
  }
  .logo-name {
    color: var(--cream);
    font-weight: 700;
    font-size: 16px;
    line-height: 1.3;
    letter-spacing: 1.5px;
    text-transform: uppercase;
    max-width: 120px;
  }

  .contact-list {
    position: absolute;
    left: 44px;
    bottom: 74px;
    list-style: none;
  }
  .contact-item {
    display: flex;
    align-items: center;
    gap: 10px;
    color: var(--white);
    font-size: 13.5px;
    line-height: 1.6;
    white-space: nowrap;
  }
  .contact-icon { width: 14px; height: 14px; flex: none; }

  .support-band {
    position: absolute;
    left: 0;
    right: 0;
    bottom: 18px;
    height: 38px;
    background: var(--yellow);
    display: flex;
    align-items: center;
    justify-content: flex-end;
    padding-right: 44px;
    color: var(--ink);
    font-size: 15px;
    font-weight: 600;
    white-space: nowrap;
  }
</style>
</head>
<body>

  <section class="card card-back" aria-label="Card back">
    <p class="back-name">Walk Beside The River</p>
  </section>

  <section class="card card-front" aria-label="Card front">
    <div class="name-block">
      <span class="name-accent"></span>
      <h1 class="person-name"><span class="first-name">Ilona</span> <span class="last-name">Marchetti</span></h1>
      <p class="person-title">CEO/Director</p>
    </div>

    <div class="logo-badge">
      <p class="logo-name">Walk Beside The River</p>
    </div>

    <ul class="contact-list">
      <li class="contact-item">
        <svg class="contact-icon" viewBox="0 0 24 24" aria-hidden="true"><path fill="#f0e82e" d="M6.6 10.8a15.1 15.1 0 0 0 6.6 6.6l2.2-2.2c.3-.3.7-.4 1-.2 1.1.4 2.3.6 3.6.6.6 0 1 .4 1 1V20c0 .6-.4 1-1 1A17 17 0 0 1 3 4c0-.6.4-1 1-1h3.5c.6 0 1 .4 1 1 0 1.3.2 2.5.6 3.6.1.3 0 .7-.2 1z"/></svg>
        0481 637 092
      </li>
      <li class="contact-item">
        <svg class="contact-icon" viewBox="0 0 24 24" aria-hidden="true"><rect x="2" y="5" width="20" height="14" rx="2" fill="none" stroke="#f0e82e" stroke-width="2"/><path d="M3 6l9 7 9-7" fill="none" stroke="#f0e82e" stroke-width="2"/></svg>
        walkbesidetheriver@mailcove.com.au
      </li>
      <li class="contact-item">
        <svg class="contact-icon" viewBox="0 0 24 24" aria-hidden="true"><path fill="none" stroke="#f0e82e" stroke-width="2" d="M12 22s7-7 7-12a7 7 0 0 0-14 0c0 5 7 12 7 12z"/><circle cx="12" cy="10" r="2.5" fill="#f0e82e"/></svg>
        PO Box 926 Kestrel Bay QLD 4590
      </li>
    </ul>

    <div class="support-band">Mental Health Support Rosalind Tavener</div>
  </section>

</body>
</html>
```